business card for a massage therapy practice named 'Cedar and Willow Massage Studio'

I really need a trendy, yet easy on the eyes business card to complement my logo. Ideally with some gold or rose gold foil work.

My uploaded file of the logo I have in horizontal but I have a vertical version as well. Another color that is used in the website is a blush pink here and there. I'd like to see some trendy tropical leaves in the design.

```html
<!DOCTYPE html>
<html lang="en">
<head>
<meta charset="utf-8">
<title>Cedar &amp; Willow Massage Studio – Business Card</title>
<link rel="stylesheet" href="https://fonts.googleapis.com/css2?family=Montserrat:wght@400;500;700&display=swap">
<style>
  :root {
    --backdrop: #c8c9cb;
    --paper: #ffffff;
    --teal: #7fc6b0;
    --gold: #a28a57;
    --ink: #1e1e1e;
    --grey: #5d5d5d;
  }
  * { margin: 0; padding: 0; box-sizing: border-box; }
  html, body { width: 1200px; height: 857px; overflow: hidden; }
  body {
    background: var(--backdrop);
    font-family: "Montserrat", sans-serif;
    display: flex;
    align-items: center;
    justify-content: center;
    gap: 40px;
  }
  .card {
    position: relative;
    width: 540px;
    height: 309px;
    overflow: hidden;
    box-shadow: 0 6px 18px rgba(0,0,0,.18);
  }
  .card--front { background: var(--paper); }
  .card--back { background: var(--teal); }

  .card__wave { position: absolute; left: 0; bottom: 0; width: 100%; height: 100px; display: block; }

  .brand {
    display: flex;
    align-items: center;
    gap: 12px;
    font-weight: 500;
    color: var(--ink);
    letter-spacing: .5px;
  }
  .brand__dot { width: 22px; height: 22px; border-radius: 50%; background: var(--gold); flex: none; }
  .brand__name { line-height: 1.25; white-space: nowrap; }

  .card--front .brand { position: absolute; top: 42px; left: 190px; font-size: 22px; }
  .card--front .brand__name span { display: block; font-size: 13px; letter-spacing: 3px; text-transform: uppercase; color: var(--teal); font-weight: 700; }

  .person { position: absolute; left: 38px; top: 150px; }
  .person__name { font-weight: 700; font-size: 20px; letter-spacing: 1.5px; color: var(--gold); text-transform: uppercase; }
  .person__role { font-size: 12px; color: var(--grey); letter-spacing: .5px; margin-top: 2px; padding-left: 14px; }

  .divider { position: absolute; left: 240px; top: 130px; width: 1px; height: 70px; background: var(--gold); }

  .contact { position: absolute; left: 262px; top: 132px; list-style: none; }
  .contact li { display: flex; align-items: center; gap: 10px; font-size: 12.5px; color: var(--grey); line-height: 22px; letter-spacing: .3px; white-space: nowrap; }
  .contact svg { width: 12px; height: 12px; flex: none; }

  .card--back .brand { position: absolute; top: 100px; left: 110px; font-size: 30px; }
  .card--back .brand__name span { display: block; font-size: 16px; letter-spacing: 4px; text-transform: uppercase; color: var(--paper); font-weight: 700; }
  .website { position: absolute; left: 0; right: 0; top: 222px; text-align: center; color: var(--paper); font-weight: 700; font-size: 13px; letter-spacing: 1px; }
</style>
</head>
<body>

  <section class="card card--front" aria-label="Business card front">
    <div class="brand">
      <span class="brand__dot"></span>
      <p class="brand__name">Cedar &amp; Willow<span>Massage Studio</span></p>
    </div>

    <div class="person">
      <p class="person__name">Owen Hale</p>
      <p class="person__role">Design Consultant</p>
    </div>

    <div class="divider"></div>

    <ul class="contact">
      <li>
        <svg viewBox="0 0 12 12" fill="none" stroke="var(--grey)" stroke-width="1.2"><rect x="3" y="1" width="6" height="10" rx="1"/><line x1="5" y1="9" x2="7" y2="9"/></svg>
        555-014-2290
      </li>
      <li>
        <svg viewBox="0 0 12 12" fill="none" stroke="var(--grey)" stroke-width="1.2"><rect x="1" y="2.5" width="10" height="7"/><polyline points="1,2.5 6,6.5 11,2.5"/></svg>
        info@cedarwillow.com
      </li>
      <li>
        <svg viewBox="0 0 12 12" fill="none" stroke="var(--grey)" stroke-width="1.1"><circle cx="6" cy="6" r="5"/><ellipse cx="6" cy="6" rx="2.2" ry="5"/><line x1="1" y1="6" x2="11" y2="6"/></svg>
        www.cedarwillowstudio.com
      </li>
    </ul>

    <svg class="card__wave" viewBox="0 0 540 100" preserveAspectRatio="none" aria-hidden="true">
      <path d="M0 86 C 170 82, 340 70, 540 26 L540 100 L0 100 Z" fill="var(--teal)"/>
      <path d="M0 77 C 160 73, 330 61, 540 14" fill="none" stroke="var(--gold)" stroke-width="3"/>
    </svg>
  </section>

  <section class="card card--back" aria-label="Business card back">
    <div class="brand">
      <span class="brand__dot"></span>
      <p class="brand__name">Cedar &amp; Willow<span>Massage Studio</span></p>
    </div>
    <p class="website">www.cedarwillowstudio.com</p>
  </section>

</body>
</html>
```